Letterhead and matching envelope design for a dental office

We need a new stationary design, letterhead and envelope #10, for a dental office in Denver area. We are called Bright Harbor Dental. We want a simple and minimalistic design but not a boring design. I wish to have one good point that makes it look professional. I have attached our logo. Feel free to use either one. I want the design for letterhead and envelope look like a "matching pair" but not look the same. The envelope doesn't have to be white and it will have an address window on bottom left.

Target Market(s)

everyone who visits dentist (adults)

Industry/Entity Type

Dental

Font styles to use
Other font styles liked:
• close to font on logo or something that matches well

Requirements
Must have
• professional
• simple, minimalistic
• unique point that stands out
Nice to have
• matching but not same design for letterhead and envelope
Should not have
• not look like all the other boring designs
• no flowery, distracting feats

```html
<!DOCTYPE html>
<html lang="en">
<head>
<meta charset="utf-8">
<title>Bright Harbor Dental – Letterhead</title>
<link rel="stylesheet" href="https://fonts.googleapis.com/css2?family=Arimo:wght@400;700&display=swap">
<style>
  :root {
    --backdrop: #dcd0cc;
    --paper: #ffffff;
    --green: #3bb34a;
    --green-soft: #b5dcb0;
    --green-faint: #e6f1e3;
    --ink: #333333;
    --ink-body: #7a7a7a;
    --rule: #9a9a9a;
  }
  * { box-sizing: border-box; margin: 0; padding: 0; }
  html, body { width: 1200px; height: 784px; overflow: hidden; }
  body {
    background: var(--backdrop);
    font-family: "Arimo", Arial, sans-serif;
    position: relative;
  }
  .letterhead {
    position: absolute;
    left: 338px;
    top: 22px;
    width: 524px;
    height: 740px;
    background: var(--paper);
    overflow: hidden;
    box-shadow: 0 2px 6px rgba(0,0,0,0.12);
  }
  .brand {
    position: absolute;
    top: 34px;
    right: 38px;
    display: flex;
    align-items: center;
    gap: 7px;
    color: var(--green);
    font-weight: 700;
    font-size: 13px;
    letter-spacing: 0.04em;
  }
  .brand-dot {
    width: 12px; height: 12px;
    border-radius: 50%;
    background: var(--green);
  }
  .contact {
    position: absolute;
    top: 104px;
    right: 38px;
    display: flex;
    gap: 10px;
    font-size: 7.5px;
    line-height: 1.45;
    color: var(--ink);
  }
  .contact-address {
    font-style: normal;
    padding-right: 10px;
    border-right: 1px solid var(--rule);
  }
  .contact-list { list-style: none; }
  .contact-list li { display: flex; align-items: center; gap: 4px; }
  .contact-icon { width: 8px; height: 8px; flex: none; }
  .letter-body {
    position: absolute;
    top: 170px;
    left: 48px;
    width: 400px;
    display: flex;
    flex-direction: column;
    gap: 12px;
    z-index: 1;
  }
  .letter {
    color: var(--ink-body);
    font-size: 9.4px;
    line-height: 1.3;
  }
  .letter-greeting {
    color: var(--ink);
    font-weight: 700;
    font-size: 10px;
    margin-bottom: 8px;
  }
  .letter p { margin-bottom: 6px; }
  .letter p:last-child { margin-bottom: 0; }
  .signature {
    width: 74px;
    height: 32px;
    margin-left: 2px;
    background: linear-gradient(90deg, #e8e8e8, #f4f4f4);
    border-radius: 3px;
  }
  .decor { position: absolute; left: 0; bottom: 0; width: 524px; height: 300px; }
</style>
</head>
<body>
  <main class="letterhead">
    <div class="brand">
      <span class="brand-dot"></span>
      <span class="brand-name">BRIGHT HARBOR DENTAL</span>
    </div>

    <div class="contact">
      <address class="contact-address">
        2150 Harbor Ridge Dr,<br>
        Suite 210 Lakewood,<br>
        CO 80228
      </address>
      <ul class="contact-list">
        <li>
          <svg class="contact-icon" viewBox="0 0 10 10"><circle cx="5" cy="5" r="5" fill="#3bb34a"/><path d="M3.3 2.6l1 1-.6.7a4 4 0 0 0 2 2l.7-.6 1 1-.8.8C4.9 7.3 2.8 5.2 2.5 3.4z" fill="#fff"/></svg>
          720-555-0148
        </li>
        <li>
          <svg class="contact-icon" viewBox="0 0 10 10"><circle cx="5" cy="5" r="5" fill="#3bb34a"/><rect x="2.4" y="3.2" width="5.2" height="3.6" fill="#fff"/><path d="M2.4 3.2L5 5.3l2.6-2.1" stroke="#3bb34a" stroke-width=".6" fill="none"/></svg>
          info@brightharbordental.com
        </li>
        <li>
          <svg class="contact-icon" viewBox="0 0 10 10"><circle cx="5" cy="5" r="5" fill="#3bb34a"/><circle cx="5" cy="5" r="2.6" stroke="#fff" stroke-width=".7" fill="none"/><path d="M2.4 5h5.2M5 2.4v5.2" stroke="#fff" stroke-width=".6"/></svg>
          www.brightharbordental.com
        </li>
      </ul>
    </div>

    <div class="letter-body">
      <section class="letter">
        <p class="letter-greeting">Dear Mr. Ellis.</p>
        <p>Lorem Ipsum is simply dummy text of the printing and typesetting industry. Lorem Ipsum has been the industry's standard dummy text ever since the 1500s, when an unknown printer took a galley of type and scrambled it to make a type specimen book. It has survived not only five centuries, but also the leap into electronic typesetting, remaining essentially unchanged.</p>
        <p>The standard chunk of Lorem Ipsum used since the 1500s is reproduced below for those interested. Sections 1.10.32 and 1.10.33 from "de Finibus Bonorum et Malorum" by Cicero are also reproduced in their exact original form, accompanied by English versions from the 1914 translation by H. Rackham.</p>
        <p>Lorem Ipsum is simply dummy text of the printing and typesetting industry. Lorem Ipsum has been the industry's standard dummy text ever since the 1500s, when an unknown printer took a galley of type and scrambled it to make a type specimen book. It has survived not only five centuries, but also the leap into electronic typesetting, remaining essentially unchanged. It was popularised in the</p>
      </section>
      <div class="signature" role="img" aria-label="Handwritten signature of the sender"></div>
    </div>

    <svg class="decor" viewBox="0 0 524 320" preserveAspectRatio="none">
      <ellipse cx="190" cy="170" rx="150" ry="95" fill="var(--green-faint)" role="img" aria-label="Faint leaf illustration decoration"/>
      <path d="M0 0 C60 40 130 150 250 230 C330 282 420 305 524 320 L0 320 Z" fill="var(--green-soft)"/>
      <path d="M0 10 C40 70 100 170 210 245 C280 292 340 310 380 320 L0 320 Z" fill="var(--paper)"/>
      <path d="M0 10 C40 70 100 170 210 245 C280 292 340 310 380 320 L330 320 C250 300 180 260 120 200 C70 150 30 80 0 40 Z" fill="var(--green)"/>
      <path d="M0 40 C30 80 70 150 120 200 C180 260 250 300 330 320 L0 320 Z" fill="var(--paper)"/>
    </svg>
  </main>
</body>
</html>
```